One of a kind, 100% Pure & Natural Skincare line needs stunning product label

We need product label design for new natural skincare company called Tolven & Mira Skincare. We create luxurious, 100% pure & natural skincare that is free from ingredients that may be potentially irritating to the skin. No toxins, preservatives or additives. Our initial product is Harbor Face Balm, a nourishing face cream that suits discerning women with mature skin and those with dry/sensitive skin needing extra hydration. Also those that choose to minimize their exposure to environmental toxins. Our brand is simple yet elegant, supporting a holistic, authentic lifestyle and embracing natural skincare.

Target Market(s)

Discerning women with mature skin and those with dry/sensitive skin needing extra hydration. Also those that choose to minimize their exposure to environmental toxins.

Industry/Entity Type

Skin Care Product

Font styles to use
Sans Serif
Script

Colors
f9d9e8
fef1ee

Requirements
Must have
• The Logo.
HARBOR FACE BALM
EMBRACING NATURAL SKINCARE
Labels must be feminine, simple/minimal yet stylish. Uncluttered yet elegant.
This is a very natural product with minimal ingredients.
Nice to have
• The logo can be incorporated in to the label, or It can be left separate as a sticker on top of the jar. The product is a firm balm consistency and is in frosted glass jars with matt silver lids.
Jar height is 45mm, width is 60mm.
Label height: 28mm and length 185mm
Should not have
• Natural or farmers market type theme. No Bold/loud lettering.

```html
<!DOCTYPE html>
<html lang="en">
<head>
<meta charset="utf-8">
<title>Harbor Face Balm – Jar Label</title>
<link href="https://fonts.googleapis.com/css2?family=Montserrat:wght@400;500;700&display=swap" rel="stylesheet">
<style>
  :root {
    --page: #ffffff;
    --ink: #1f1f1f;
    --ink-soft: #2c2c2c;
    --trim: #8a8a8a;
    --bleed: #b9d3e6;
    --pink-deep: #f2bfcd;
    --pink-mid: #f9d9e8;
    --pink-pale: #fef1ee;
    --white: #ffffff;
  }
  * { box-sizing: border-box; margin: 0; padding: 0; }
  html, body {
    width: 1200px; height: 1000px; overflow: hidden;
    background: var(--page);
    font-family: "Montserrat", sans-serif;
    color: var(--ink);
  }
  .label-sheet {
    position: absolute; left: 40px; top: 399px;
    width: 1120px; height: 202px;
    border: 1px dashed var(--bleed);
  }
  .label-trim {
    position: absolute; left: 18px; top: 17px;
    width: 1097px; height: 167px;
    border: 1px solid var(--trim);
    background: var(--white);
    overflow: hidden;
  }
  .safe-area {
    position: absolute; top: 17px; height: 134px;
    border: 1px dashed var(--bleed);
  }
  .safe-area--left { left: 18px; width: 320px; border-right: none; }
  .safe-area--right { left: 742px; width: 336px; border-left: none; }
  .info-panel {
    position: absolute; top: 25px;
    font-size: 9.5px; line-height: 1.35; color: var(--ink-soft);
  }
  .info-panel p { margin-bottom: 10px; }
  .info-panel strong { font-weight: 700; color: var(--ink); }
  .info-panel--left { left: 25px; width: 290px; }
  .info-panel--right { left: 753px; width: 320px; }
  .front-panel {
    position: absolute; left: 349px; top: 0;
    width: 383px; height: 100%;
    background: linear-gradient(90deg, var(--pink-deep) 0%, var(--pink-mid) 45%, var(--pink-pale) 75%, var(--white) 100%);
    text-align: center;
  }
  .product-name {
    margin-top: 55px;
    font-size: 27px; font-weight: 400; letter-spacing: 0.5px; color: var(--ink);
  }
  .product-rule {
    width: 224px; height: 1px; background: var(--ink);
    margin: 3px auto 6px;
  }
  .product-tagline {
    font-size: 11.5px; letter-spacing: 0.4px; color: var(--ink-soft);
  }
  .net-weight {
    margin-top: 20px; font-size: 6px; color: var(--ink-soft);
  }
  .contact-line { display: flex; align-items: center; gap: 5px; }
  .pao-icon { position: absolute; left: 1040px; top: 130px; }
</style>
</head>
<body>
  <div class="label-sheet">
    <div class="label-trim">
      <div class="safe-area safe-area--left"></div>
      <div class="safe-area safe-area--right"></div>

      <div class="info-panel info-panel--left">
        <p><strong>INGREDIENTS :</strong>&nbsp; Tallow from pasture raised goats, frankincense, sandalwood &amp; myrrh essential oils.</p>
        <p><strong>DIRECTIONS :</strong>&nbsp; Soften small amount in palm of<br>hand &amp; gently massage into skin as often as</p>
        <p style="margin-top:14px">Allergy patch test recommended. If irritation occurs, discon-<br>tinue use.</p>
      </div>

      <div class="front-panel">
        <h1 class="product-name">HARBOR FACE BALM</h1>
        <div class="product-rule"></div>
        <p class="product-tagline">EMBRACING NATURAL SKINCARE</p>
        <p class="net-weight">NET WT 1.76 oz</p>
      </div>

      <div class="info-panel info-panel--right">
        <p><strong>CAUTION:</strong>&nbsp; Keep out of reach of children. If pregnant or breastfeeding, consult your healthcare practitioner. Avoid contact with eyes &amp; sensitive areas.</p>
        <p>Store below 25°C</p>
        <p>MADE IN AUSTRALIA</p>
        <p>B#</p>
        <p class="contact-line">
          <svg width="13" height="9" viewBox="0 0 13 9" aria-hidden="true"><rect x="0.5" y="0.5" width="12" height="8" fill="none" stroke="#1f1f1f"/><path d="M0.5 0.5 L6.5 5 L12.5 0.5" fill="none" stroke="#1f1f1f"/></svg>
          info@tolvenandmiraskincare.com.au
        </p>
      </div>

      <svg class="pao-icon" width="24" height="20" viewBox="0 0 24 20" role="img" aria-label="Period after opening 6 months">
        <path d="M3 6 L21 6 L21 19 L3 19 Z" fill="none" stroke="#1f1f1f" stroke-width="1"/>
        <path d="M4 4 L19 0.5" stroke="#1f1f1f" stroke-width="1.2"/>
        <text x="12" y="16" font-family="Montserrat, sans-serif" font-size="6" font-weight="700" text-anchor="middle" fill="#1f1f1f">6M</text>
      </svg>
    </div>
  </div>
</body>
</html>
```